Restyle corporate identity (+ logo) for a road construction company

We need a new logo and stationary design for our company VARNOK path. VARNOK path® increases the road base strength, while reducing major costs and time of road construction. Attached some examples of the current design.

Our wishes for the new logo:
- Business look
- Style sheet
- Modern

More information: www.varnokpath.example
Updates

Target Market(s)

Government

Industry/Entity Type

Construction

Requirements
Must have
• Logo (with road sign) + text

```html
<!DOCTYPE html>
<html lang="en">
<head>
<meta charset="utf-8">
<title>VARNOK path stationery</title>
<link href="https://fonts.googleapis.com/css2?family=Saira+Condensed:wght@600&family=Arimo:wght@400;700&display=swap" rel="stylesheet">
<style>
:root{
  --bg:#eef0ef;
  --paper:#ffffff;
  --green:#9cc31f;
  --grey:#8f8f8f;
  --dark:#4a4a4a;
  --ink:#333333;
  --shadow:0 6px 14px rgba(0,0,0,.18);
}
*{margin:0;padding:0;box-sizing:border-box}
html,body{width:1200px;height:937px;overflow:hidden;background:var(--bg);font-family:'Arimo',Arial,sans-serif;color:var(--ink)}
.sheet{position:absolute;background:var(--paper);box-shadow:var(--shadow);overflow:hidden}
.wave{position:absolute;left:0;bottom:0;width:100%}
.brand{position:absolute;display:flex;align-items:center;gap:.3em;font-family:'Saira Condensed',sans-serif;font-weight:600;color:var(--grey);white-space:nowrap;letter-spacing:.02em}
.brand .dot{width:1.3em;height:1.3em;border-radius:50%;background:var(--green);flex:none}
.site{position:absolute;color:#fff;font-size:10px;letter-spacing:.22em}
.letterhead{left:185px;top:66px;width:388px;height:546px}
.letterhead .brand{left:18px;top:24px;font-size:36px}
.contact{position:absolute;right:12px;top:22px;font-size:5px;line-height:8px;text-align:right;color:#444}
.letter{position:absolute;left:37px;top:140px;width:300px;font-size:5.4px;line-height:7.4px;color:#444}
.letter p{margin-bottom:9px}
.signature{width:24px;height:14px;background:#e6e6e6;margin:6px 0 4px}
.folder{left:636px;top:40px;width:458px;height:577px}
.folder .brand{left:86px;top:270px;font-size:64px;flex-direction:column;gap:18px}
.folder .brand .dot{width:104px;height:104px}
.folder .site{left:22px;bottom:12px;font-size:10px}
.card{width:177px;height:100px;border-radius:6px}
.card-front{left:45px;top:658px}
.card-front .brand{left:12px;top:10px;font-size:13px;flex-direction:column;gap:3px}
.card-front .brand .dot{width:20px;height:20px}
.card-front .person{position:absolute;left:100px;top:10px;font-size:4.6px;line-height:6.2px;color:#444}
.card-front .person b{font-size:5.2px;color:var(--ink)}
.card-front .address{position:absolute;left:8px;bottom:7px;font-size:5px;line-height:7px;color:#fff}
.card-back{left:45px;top:785px;height:99px}
.card-back .brand{left:34px;top:37px;font-size:20px}
.envelope{left:265px;top:672px;width:432px;height:209px}
.envelope .brand{left:14px;top:20px;font-size:30px}
.envelope .site{left:14px;bottom:10px;font-size:9px}
.envelope-back{left:737px;top:672px;width:432px;height:209px}
.flap{position:absolute;left:0;top:0;width:100%;height:72px;background:var(--green);border-radius:0 0 40px 40px}
.flap .site{left:0;right:0;top:28px;text-align:center;font-size:12px}
</style>
</head>
<body>

<section class="sheet letterhead">
  <div class="brand"><span class="dot"></span>VARNOK path</div>
  <div class="contact">Unit 12 Carrow Yard<br>Mill Lane, Westbury<br>012 345 6789<br>012 345 6789<br>012 345 6789<br>mail@varnokpath.example<br>www.varnokpath.example</div>
  <div class="letter">
    <p>July 2, 2012</p>
    <p><b>Dear Sir,</b><br>ABC Building, def St., Country Name</p>
    <p>is simply dummy text of the printing and typesetting industry. Lorem Ipsum has been the industry's standard dummy text ever since the 1500s, when an unknown printer took a galley of type and scrambled it to make a type specimen book. It has survived not only five centuries, but also the leap into electronic typesetting, remaining essentially unchanged. It was popularised in the 1960s with the release of Letraset sheets containing Lorem Ipsum passages, and more recently with desktop publishing software including versions of Lorem Ipsum.</p>
    <p>is simply dummy text of the printing and typesetting industry. Lorem Ipsum has been the industry's standard dummy text ever since the 1500s, when an unknown printer took a galley of type and scrambled it to make</p>
    <p style="margin-top:22px">is simply dummy text of the printing and typesetting industry. Lorem Ipsum has been the industry's standard dummy text ever since the 1500s, when an unknown printer took a galley of type and scrambled it to make a type specimen book. It has survived not only five centuries, but also the leap into electronic typesetting, remaining essentially unchanged. It was popularised in the 1960s with the release of Letraset sheets containing Lorem Ipsum passages, and more recently with desktop publishing software including versions of Lorem Ipsum.</p>
    <p>Best Regards,</p>
    <div class="signature" role="img" aria-label="Handwritten signature"></div>
    <p><b>Dorin Kessel</b><br>Director<br><br>ABC Building, def St., Country Name</p>
  </div>
  <svg class="wave" viewBox="0 0 400 100" preserveAspectRatio="none" height="100">
    <path d="M0 48 C110 10 260 20 400 0 L400 100 L0 100Z" fill="var(--green)"/>
    <path d="M0 40 C110 2 260 12 400 -8 L400 2 C260 22 110 14 0 46Z" fill="var(--dark)"/>
    <path d="M20 50 C130 14 270 26 400 10 L400 13 C270 30 130 20 20 50Z" fill="var(--grey)"/>
  </svg>
</section>

<section class="sheet folder">
  <div class="brand"><span class="dot"></span>VARNOK path</div>
  <svg class="wave" viewBox="0 0 400 100" preserveAspectRatio="none" height="100">
    <path d="M0 48 C110 10 260 20 400 0 L400 100 L0 100Z" fill="var(--green)"/>
    <path d="M0 40 C110 2 260 12 400 -8 L400 2 C260 22 110 14 0 46Z" fill="var(--dark)"/>
    <path d="M20 50 C130 14 270 26 400 10 L400 13 C270 30 130 20 20 50Z" fill="var(--grey)"/>
  </svg>
  <div class="site">www.varnokpath.example</div>
</section>

<section class="sheet card card-front">
  <div class="brand"><span class="dot"></span>VARNOK path</div>
  <div class="person"><b>TOMAS REYLAND</b><br>Managing Director<br><br>012 345 6789<br>012 345 6789<br>012 345 6789<br>mail@varnokpath.example</div>
  <svg class="wave" viewBox="0 0 400 100" preserveAspectRatio="none" height="34">
    <path d="M0 48 C110 10 260 20 400 0 L400 100 L0 100Z" fill="var(--green)"/>
    <path d="M0 40 C110 2 260 12 400 -8 L400 2 C260 22 110 14 0 46Z" fill="var(--dark)"/>
  </svg>
  <div class="address">Unit 12 Carrow Yard<br>Mill Lane, Westbury</div>
</section>

<section class="sheet card card-back">
  <div class="brand"><span class="dot"></span>VARNOK path</div>
</section>

<section class="sheet envelope">
  <div class="brand"><span class="dot"></span>VARNOK path</div>
  <svg class="wave" viewBox="0 0 400 100" preserveAspectRatio="none" height="90">
    <path d="M0 48 C110 10 260 20 400 0 L400 100 L0 100Z" fill="var(--green)"/>
    <path d="M0 40 C110 2 260 12 400 -8 L400 2 C260 22 110 14 0 46Z" fill="var(--dark)"/>
    <path d="M20 50 C130 14 270 26 400 10 L400 13 C270 30 130 20 20 50Z" fill="var(--grey)"/>
  </svg>
  <div class="site">www.varnokpath.example</div>
</section>

<section class="sheet envelope-back">
  <div class="flap"><div class="site">www.varnokpath.example</div></div>
</section>

</body>
</html>
```